Social Media Graphics - Oakline Push REVISED

Create 6-7 individual social media graphics (square size) to encourage folks to join our online course called:

The Harvest Ledger Circle
How to Launch a Multi-Million Business From Scratch
Sign Up Today!

IMPORTANT: Make the largest and most prominent text on the graphic be: How to Launch a Multi-Million Business From Scratch

For the color scheme of the graphics, let's try a blue color palette; make sure the graphics appeal to both men and women

Make sure each graphic contains 1 of the 3 pics attached (crop pic as needed); and make sure one of the graphics is all TEXT only.

Target Market(s)

men and women looking to start a business

Industry/Entity Type

Entrepreneurship

Colors
0054AA
0677BA
7BADD7
CADEEF
E8F1F8

Requirements
Must have
• All the text and use the 3 pics provided; one graphic can be all text; Simple, modern design that's easy to read

```html
<!DOCTYPE html>
<html lang="en">
<head>
<meta charset="utf-8">
<title>The Harvest Ledger Circle – Social Graphics</title>
<link href="https://fonts.googleapis.com/css2?family=Bebas+Neue&family=Barlow+Condensed:ital,wght@1,600&display=swap" rel="stylesheet">
<style>
  :root{
    --blue-deep:#0054AA;
    --blue-mid:#0677BA;
    --blue-soft:#7BADD7;
    --blue-pale:#CADEEF;
    --blue-mist:#E8F1F8;
    --white:#ffffff;
    --page:#ffffff;
  }
  *{box-sizing:border-box;margin:0;padding:0}
  html,body{width:1200px;height:902px;overflow:hidden;background:var(--page)}
  .board{position:relative;width:1200px;height:902px}
  .tile{position:absolute;width:312px;height:312px;overflow:hidden;background:var(--blue-deep)}
  .tile--1{left:119px;top:143px}
  .tile--2{left:463px;top:143px}
  .tile--3{left:807px;top:143px}
  .tile--4{left:119px;top:486px}
  .tile--5{left:463px;top:486px}
  .tile--6{left:807px;top:486px}
  .backdrop{position:absolute;inset:0;width:312px;height:312px}
  .series-title{
    position:absolute;left:0;right:0;top:12px;text-align:center;
    font-family:"Barlow Condensed",sans-serif;font-style:italic;font-weight:600;
    font-size:28px;line-height:32px;color:var(--white);text-transform:uppercase;letter-spacing:-0.3px;
  }
  .headline{
    position:absolute;left:0;right:0;top:177px;text-align:center;
    font-family:"Bebas Neue",sans-serif;font-size:36px;line-height:40px;color:var(--white);
    letter-spacing:-0.2px;
  }
  .photo{position:absolute;border-radius:4px}
  .photo--studio{background:linear-gradient(160deg,#1b2b44 0%,#2c3f5e 45%,#16335f 100%)}
  .photo--colour{background:linear-gradient(160deg,#b33a55 0%,#d94a6a 40%,#1d1d24 100%)}
  .photo--stage{background:linear-gradient(160deg,#2d4a80 0%,#8a8474 50%,#e4e4e4 100%)}
  .badge{
    position:absolute;border-radius:50%;background:var(--blue-deep);
    border:2px solid var(--white);box-shadow:0 0 0 2px var(--blue-deep),0 0 8px rgba(0,0,0,.35);
    display:flex;flex-direction:column;align-items:center;justify-content:center;
    font-family:"Bebas Neue",sans-serif;color:var(--white);text-align:center;
  }
  .badge span{display:block}
  .tile--3 .series-title{left:16px;top:22px;text-align:left;font-size:28px;text-shadow:2px 2px 3px rgba(0,0,0,.45)}
  .tile--3 .frame{position:absolute;inset:5px;border:1.5px solid var(--white)}
  .tile--3 .headline{left:16px;top:70px;text-align:left;font-size:44px;line-height:48px;text-shadow:2px 2px 3px rgba(0,0,0,.45)}
  .tile--5{background:radial-gradient(circle at 50% 45%,var(--blue-mid) 0%,#0a63b0 45%,var(--blue-deep) 100%)}
  .tile--6 .series-title{left:20px}
</style>
</head>
<body>
<main class="board">

  <!-- Tile 1: arc header -->
  <section class="tile tile--1">
    <svg class="backdrop" viewBox="0 0 312 312"><path d="M0 0H312V40Q156 300 0 46Z" fill="var(--blue-mid)"/><path d="M312 40Q156 300 0 46" fill="none" stroke="var(--blue-pale)" stroke-width="1.5"/></svg>
    <h2 class="series-title">The Harvest Ledger Circle</h2>
    <div class="photo photo--studio" role="img" aria-label="Photo of the two course hosts standing together, arms crossed" style="left:55px;top:48px;width:156px;height:126px"></div>
    <div class="badge" style="left:229px;top:78px;width:58px;height:58px;font-size:21px;line-height:18px"><span>Sign Up</span><span>Today!</span></div>
    <h1 class="headline">How to Launch a<br>Multi-Million Business<br>From Scratch</h1>
  </section>

  <!-- Tile 2: diagonal band -->
  <section class="tile tile--2">
    <svg class="backdrop" viewBox="0 0 312 312"><polygon points="0,0 312,0 312,312 260,312 40,0" fill="var(--blue-mid)"/><polygon points="0,0 40,0 260,312 0,312" fill="var(--blue-deep)"/><polygon points="312,140 312,312 200,312" fill="var(--blue-deep)"/></svg>
    <h2 class="series-title">The Harvest Ledger Circle</h2>
    <div class="photo photo--colour" role="img" aria-label="Photo of the two course hosts, one in a pink dress and one in a black jacket" style="left:140px;top:48px;width:142px;height:142px"></div>
    <div class="badge" style="left:40px;top:76px;width:82px;height:82px;font-size:30px;line-height:26px"><span>Sign Up</span><span>Today!</span></div>
    <h1 class="headline">How to Launch a<br>Multi-Million Business<br>From Scratch</h1>
  </section>

  <!-- Tile 3: text only -->
  <section class="tile tile--3">
    <svg class="backdrop" viewBox="0 0 312 312">
      <circle cx="280" cy="40" r="55" fill="var(--blue-mid)" opacity=".7"/>
      <circle cx="110" cy="65" r="12" fill="var(--blue-mid)" opacity=".7"/>
      <circle cx="280" cy="173" r="18" fill="var(--blue-mid)" opacity=".8"/>
      <circle cx="20" cy="280" r="30" fill="var(--blue-mid)" opacity=".7"/>
      <circle cx="110" cy="283" r="12" fill="var(--blue-mid)" opacity=".8"/>
      <circle cx="160" cy="300" r="20" fill="var(--blue-mid)" opacity=".7"/>
      <circle cx="155" cy="233" r="10" fill="var(--blue-mid)" opacity=".8"/>
    </svg>
    <div class="frame"></div>
    <h2 class="series-title">The Harvest Ledger Circle</h2>
    <h1 class="headline">How to Launch<br>a Multi-Million<br>Business From<br>Scratch</h1>
    <div class="badge" style="left:206px;top:218px;width:74px;height:74px;font-size:27px;line-height:24px"><span>Sign Up</span><span>Today!</span></div>
  </section>

  <!-- Tile 4: stage panel -->
  <section class="tile tile--4">
    <svg class="backdrop" viewBox="0 0 312 312"><polygon points="0,215 42,163 242,163 312,210 312,312 0,312" fill="var(--blue-mid)"/><polyline points="0,215 42,163 242,163 312,210" fill="none" stroke="var(--blue-pale)" stroke-width="1.5"/></svg>
    <h2 class="series-title">The Harvest Ledger Circle</h2>
    <div class="photo photo--stage" role="img" aria-label="Photo of the two course hosts speaking on stage with microphones" style="left:42px;top:57px;width:171px;height:106px"></div>
    <div class="badge" style="left:222px;top:74px;width:58px;height:58px;font-size:21px;line-height:18px"><span>Sign Up</span><span>Today!</span></div>
    <h1 class="headline" style="top:182px">How to Launch a<br>Multi-Million Business<br>From Scratch</h1>
  </section>

  <!-- Tile 5: radial glow -->
  <section class="tile tile--5">
    <h2 class="series-title">The Harvest Ledger Circle</h2>
    <div class="photo photo--studio" role="img" aria-label="Photo of the two course hosts standing together, arms crossed" style="left:71px;top:54px;width:169px;height:134px"></div>
    <div class="badge" style="left:236px;top:71px;width:58px;height:58px;font-size:21px;line-height:18px"><span>Sign Up</span><span>Today!</span></div>
    <h1 class="headline">How to Launch a<br>Multi-Million Business<br>From Scratch</h1>
  </section>

  <!-- Tile 6: swoop header -->
  <section class="tile tile--6">
    <svg class="backdrop" viewBox="0 0 312 312"><path d="M0 0H312V182Q60 190 0 0Z" fill="var(--blue-mid)"/><path d="M312 182Q60 190 0 0" fill="none" stroke="var(--blue-pale)" stroke-width="1.5"/></svg>
    <h2 class="series-title">The Harvest Ledger Circle</h2>
    <div class="photo photo--stage" role="img" aria-label="Photo of the two course hosts speaking on stage with microphones" style="left:114px;top:46px;width:169px;height:136px"></div>
    <div class="badge" style="left:35px;top:71px;width:58px;height:58px;font-size:21px;line-height:18px"><span>Sign Up</span><span>Today!</span></div>
    <h1 class="headline" style="top:184px">How to Launch a<br>Multi-Million Business<br>From Scratch</h1>
  </section>

</main>
</body>
</html>
```